PDF flyer for our companies' two main products: Food processing machines.

PDF flyer with showcasing two products. Flyer can be one page per product, or both products on the same page.

Product #1: Labeled "Ribbon blenders".
Showing a photo of the machine, and the details/features offered with that machine. Product description must also say: "Sizes available; 2 Cu Ft. - 450 Cu Ft."

Product #2: Labeled: " Auger hoppers / Screw feeders"
Showing a photo of the machine, and the details/features offered with that machine.

SEE UPLOADED IMAGES; "Ribbon Blenders EXAMPLE FLYER".
& "Auger Hoppers / Screw Conveyors EXAMPLE FLYER" for a rough idea of what we are looking for.

Target Market(s)

Copackers, Packing houses, Food manufacturers, protein powder producers,

Industry/Entity Type

Commercial Food processing / packing / mixing equipment

Font styles to use
Serif

Colors
0054AA
0677BA
7BADD7
CADEEF
E8F1F8

Requirements
Must have
• Company logo on top of flyer.
Nice to have
• I would like for the flyer to show some stock images of common ingredients, similar to the images uploaded.
Should not have
• Pictures with background. Backgrounds must be removed from provides photos. "clipping path"

```html
<!DOCTYPE html>
<html lang="en">
<head>
<meta charset="utf-8">
<title>Keelstone Equipment – Product Flyers</title>
<link href="https://fonts.googleapis.com/css2?family=Saira+Semi+Condensed:wght@500;600;700&family=Sora:wght@400;500&display=swap" rel="stylesheet">
<style>
:root{
  --navy:#0054AA;
  --blue:#1A9BE3;
  --mid:#0677BA;
  --sky:#7BADD7;
  --mist:#CADEEF;
  --ice:#E8F1F8;
  --ink:#1d1d1f;
  --body:#2c2c2c;
  --stage:#dcdde2;
  --paper:#ffffff;
}
*{margin:0;padding:0;box-sizing:border-box}
html,body{width:1200px;height:772px;overflow:hidden;background:var(--stage)}
body{position:relative;font-family:"Sora",sans-serif;color:var(--body)}
.page{position:absolute;top:80px;width:432px;height:610px;background:var(--paper);overflow:hidden;box-shadow:0 2px 8px rgba(0,0,0,.12)}
.page--auger{left:150px}
.page--blender{left:616px}
.abs{position:absolute}
.heading{font-family:"Saira Semi Condensed",sans-serif;font-weight:500;color:var(--ink);line-height:1.3}
.section-title{font-family:"Saira Semi Condensed",sans-serif;font-weight:500;color:var(--blue);font-size:12.5px}
.feature-list{list-style:none;font-size:6.9px;line-height:13.7px;color:var(--body)}
.feature-list li{position:relative;padding-left:12px}
.feature-list li::before{content:"";position:absolute;left:0;top:6px;width:6px;height:1.2px;background:var(--blue)}
.feature-list li::after{content:"";position:absolute;left:4px;top:4.8px;border-left:3px solid var(--blue);border-top:1.8px solid transparent;border-bottom:1.8px solid transparent}
.feature-list li.plain::before,.feature-list li.plain::after{display:none}
.brand{display:flex;align-items:center;gap:5px;font-family:"Sora",sans-serif;font-weight:500;font-size:13px;letter-spacing:1.5px;color:var(--ink)}
.brand__dot{width:9px;height:9px;border-radius:50%;background:var(--navy)}
.photo{border-radius:3px}
.spec-card{background:#fff;box-shadow:0 1px 5px rgba(0,0,0,.22)}
.spec-table{border-collapse:collapse;font-family:Arial,sans-serif;color:#000}
.spec-table td{border:.6px solid #000;padding:0 1px;white-space:nowrap}
/* auger page */
.auger__panel{left:170px;top:0;width:262px;height:280px;background:var(--blue);border-radius:0 0 130px 160px}
.auger__intro{left:188px;top:74px;width:228px;text-align:center;color:#fff;font-family:"Saira Semi Condensed",sans-serif;font-size:6.6px;line-height:13.7px}
.auger__title{left:20px;top:55px;width:145px;text-align:center;font-size:19px}
.dots{background:var(--navy);opacity:.75}
.auger__ingredients{left:0;width:432px;top:448px;text-align:center;font-family:"Saira Semi Condensed",sans-serif;font-weight:700;color:var(--navy);font-size:27px}
.dot-band{left:0;top:570px;width:432px;height:40px;background:#e4e6ea}
/* blender page */
.blender__title{left:242px;top:56px;width:155px;text-align:center;font-size:20px}
.size-badge{left:253px;top:92px;width:122px;height:36px;background:var(--navy);color:#fff;text-align:center;font-family:"Saira Semi Condensed",sans-serif;font-size:10px;line-height:15px;padding-top:3px;border-radius:10px 0 10px 0;box-shadow:3px -3px 0 -1px #fff,4px -4px 0 -1px var(--blue)}
.blender__vertical{left:-28px;top:200px;width:110px;transform:rotate(90deg);font-family:"Saira Semi Condensed",sans-serif;font-weight:700;font-size:22px;color:var(--sky);opacity:.55;text-align:center}
.bottom-band{left:0;top:545px;width:432px;height:65px;background:var(--ice)}
</style>
</head>
<body>

<!-- Page one: auger hoppers -->
<section class="page page--auger">
  <div class="abs dots" style="left:8px;top:8px;width:45px;height:45px;clip-path:polygon(0 0,100% 0,0 100%)"></div>
  <div class="abs auger__panel"></div>
  <div class="abs brand" style="left:236px;top:31px"><span class="brand__dot"></span>KEELSTONE</div>
  <p class="abs auger__intro">Lorem ipsum dolor sit amet, consectetur adipiscing elit, sed do eiusmod tempor incididunt ut labore et dolore magna aliqua. Ut enim ad minim veniam, quis nostrud exercitation ullamco laboris nisi ut aliquip ex ea commodo consequat. Duis aute irure dolor in reprehenderit in voluptate velit esse cillum dolore eu fugiat nulla pariatur. Excepteur sint occaecat cupidatat non proident, sunt in culpa qui officia deserunt mollit anim id est laborum</p>
  <h1 class="abs heading auger__title">Auger Hoppers / Screw Feeders</h1>
  <div class="abs photo" role="img" aria-label="Stainless steel auger hopper with inclined screw feeder tube on castor wheels" style="left:112px;top:125px;width:232px;height:295px;background:radial-gradient(ellipse at 60% 65%,rgba(170,172,176,.85),rgba(190,192,196,.35) 55%,rgba(255,255,255,0) 72%)"></div>
  <div class="abs dots" style="left:382px;top:290px;width:45px;height:45px;clip-path:polygon(0 0,100% 0,0 100%)"></div>

  <h2 class="abs section-title" style="left:24px;top:185px">Standard Features</h2>
  <ul class="abs feature-list" style="left:24px;top:209px;width:160px">
    <li>Direct Drive</li>
    <li>304 Stainless Steel Construction</li>
    <li>Stainless Steel Safety grating</li>
    <li>Pre-wired control panel</li>
    <li>Electric Vibrator</li>
    <li>Castor Wheels</li>
  </ul>
  <h2 class="abs section-title" style="left:24px;top:312px">Options</h2>
  <ul class="abs feature-list" style="left:24px;top:336px;width:160px">
    <li>Square or round hopper 3.5cf and 7cf hopper are standard</li>
    <li>Custom hoppers upto 200cf</li>
    <li>VFD (Variable Frequency Drive)</li>
    <li>Clamshell Auger Tube for easy cleanout</li>
    <li>316 Stainless Steel Construction</li>
  </ul>

  <div class="abs spec-card" style="left:199px;top:359px;width:208px;height:61px;padding:9px 12px">
    <table class="spec-table" style="font-size:3.3px;width:184px;line-height:5px">
      <tr><td>MODEL</td><td>AH-A2</td><td>AH-A3</td><td>AH-A5</td><td>AH-A7</td><td>AH-A8</td><td>AH-A12</td></tr>
      <tr><td>FEEDING RATE</td><td>2m³/hr</td><td>3m³/hr</td><td>5m³/hr</td><td>7m³/hr</td><td>8m³/hr</td><td>12m³/hr</td></tr>
      <tr><td>PIPE DIAMETER</td><td>4"</td><td>4-1/2"</td><td>5-1/2"</td><td>6-1/4"</td><td>6-1/2"</td><td>8-1/2"</td></tr>
      <tr><td>HOPPER VOL.</td><td>3.5CF</td><td colspan="5" style="text-align:center">7CF</td></tr>
      <tr><td>DIMENSIONS</td><td>28.6"x24.4"x31.5"</td><td colspan="5" style="text-align:center">40" x 32" x 35"</td></tr>
      <tr><td>TOTAL WEIGHT</td><td>221LBS</td><td>287LBS</td><td>397LBS</td><td>441LBS</td><td>485LBS</td><td>596LBS</td></tr>
      <tr><td>CHARGING HEIGHT</td><td colspan="6" style="text-align:center">STANDARD 72 INCHES. (40" - 196" AVAILABLE)</td></tr>
      <tr><td>CHARGING ANGLE</td><td colspan="6" style="text-align:center">STANDARD 45° (30°-60° AVAILABLE)</td></tr>
    </table>
  </div>

  <h2 class="abs auger__ingredients">Ingredients</h2>
  <div class="abs photo" role="img" aria-label="Whole mixed spices" style="left:40px;top:492px;width:62px;height:58px;background:radial-gradient(circle,#9a6a3c 30%,rgba(255,255,255,0) 70%)"></div>
  <div class="abs photo" role="img" aria-label="Pile of ground spice powder" style="left:115px;top:492px;width:88px;height:58px;background:radial-gradient(ellipse at 50% 60%,#a8703e 35%,rgba(255,255,255,0) 70%)"></div>
  <div class="abs photo" role="img" aria-label="Pile of black peppercorns" style="left:218px;top:495px;width:84px;height:52px;background:radial-gradient(ellipse,#2a221c 40%,rgba(255,255,255,0) 72%)"></div>
  <div class="abs photo" role="img" aria-label="Bowls of assorted spices and seeds" style="left:318px;top:490px;width:78px;height:60px;background:radial-gradient(ellipse,#b89360 30%,rgba(255,255,255,0) 72%)"></div>
  <div class="abs dot-band"></div>
</section>

<!-- Page two: ribbon blenders -->
<section class="page page--blender">
  <div class="abs" role="img" aria-label="Faint background of spices on wooden spoons" style="left:0;top:0;width:432px;height:170px;background:linear-gradient(180deg,#fbf8f5,#f6f1ec)"></div>
  <svg class="abs" style="left:0;top:0" width="432" height="610" aria-hidden="true">
    <polygon points="0,140 432,168 432,300 0,272" fill="var(--blue)"/>
  </svg>
  <div class="abs dots" style="left:16px;top:15px;width:30px;height:30px;clip-path:polygon(0 0,100% 0,0 100%)"></div>
  <div class="abs photo" role="img" aria-label="Stainless steel ribbon blender with control box on a wheeled frame" style="left:60px;top:8px;width:192px;height:228px;background:radial-gradient(ellipse at 50% 45%,rgba(165,168,172,.9),rgba(190,192,196,.4) 55%,rgba(255,255,255,0) 72%)"></div>
  <div class="abs brand" style="left:272px;top:24px"><span class="brand__dot"></span>KEELSTONE</div>
  <h1 class="abs heading blender__title">Ribbon Blenders</h1>
  <div class="abs size-badge">Sizes Available;<br>2 Cu Ft. – 450 Cu Ft.</div>
  <div class="abs photo" role="img" aria-label="Measuring spoons filled with spices" style="left:372px;top:112px;width:60px;height:58px;background:radial-gradient(circle,#c0662a 25%,rgba(255,255,255,0) 70%)"></div>

  <div class="abs blender__vertical">Ingredients</div>
  <div class="abs photo" role="img" aria-label="Spice jars on a wooden shelf" style="left:52px;top:160px;width:72px;height:108px;transform:rotate(1.5deg);background:linear-gradient(160deg,#3d2a1e,#6a4a32 55%,#2a1c14)"></div>
  <div class="abs photo" role="img" aria-label="Bowls of turmeric, paprika and curry powder" style="left:137px;top:164px;width:72px;height:108px;transform:rotate(1.5deg);background:linear-gradient(170deg,#2f3440,#c98a2a 55%,#2f3440)"></div>
  <div class="abs photo" role="img" aria-label="Assorted spices laid out on a grey table" style="left:222px;top:168px;width:72px;height:108px;transform:rotate(1.5deg);background:linear-gradient(170deg,#d8d8d8,#b07856 50%,#d4d4d4)"></div>
  <div class="abs photo" role="img" aria-label="Wooden spoon of red spice powder" style="left:307px;top:172px;width:72px;height:108px;transform:rotate(1.5deg);background:linear-gradient(175deg,#b2532b,#d59a6f 50%,#e8e3de)"></div>
  <div class="abs photo" role="img" aria-label="Scoop spilling chili powder" style="left:145px;top:283px;width:72px;height:58px;background:radial-gradient(ellipse at 55% 60%,#b8361f 30%,rgba(255,255,255,0) 70%)"></div>

  <h2 class="abs section-title" style="left:25px;top:312px">Standard Features</h2>
  <ul class="abs feature-list" style="left:25px;top:333px;width:200px">
    <li>304 Stainless Steel Construction</li>
    <li class="plain">Pre-wired control panel with; batch timer, on/off</li>
    <li>switch, emergency stop button</li>
    <li>Food grade compression shaft seals</li>
    <li>Safety sensor on lid for automatic shutoff when opened</li>
    <li>Air acutated discharge valve</li>
    <li>1 Piece hinged lid with safety granting</li>
    <li>Power options; 220v/480v</li>
    <li>24” Standard discharge height</li>
    <li>Castor wheels on 53cf units and smaller</li>
  </ul>
  <h2 class="abs section-title" style="left:230px;top:312px">Options</h2>
  <ul class="abs feature-list" style="left:230px;top:333px;width:195px">
    <li>Dual hinged lids available on custom order</li>
    <li>Knife gate style discharge available on custom orders</li>
    <li>Air pure seals available on custom orders</li>
    <li>316 Stainless materials avaiable on custom orders</li>
    <li>Custom height modification</li>
    <li>Liquid spary systems</li>
    <li>(VFD) Variable Frequency Drives</li>
    <li>Leg extensions</li>
  </ul>

  <div class="abs bottom-band"></div>
  <div class="abs photo" role="img" aria-label="Bowl of whole cloves" style="left:362px;top:476px;width:70px;height:62px;background:radial-gradient(ellipse,#5a3a26 30%,rgba(255,255,255,0) 70%)"></div>
  <div class="abs spec-card" style="left:68px;top:497px;width:295px;height:96px;padding:8px 0 0 31px">
    <table class="spec-table" style="font-size:3px;width:232px;line-height:4.9px">
      <tr><td><b>Model Size</b></td><td><b>5cf</b></td><td><b>7CF</b></td><td><b>10.5CF</b></td><td><b>17.5CF</b></td><td><b>35CF</b></td><td><b>53CF</b></td><td><b>70.5CF</b></td><td><b>106CF</b></td></tr>
      <tr><td>Working Liters</td><td>120L</td><td>200L</td><td>300L</td><td>500L</td><td>1000L</td><td>1500L</td><td>2000L</td><td>3000L</td></tr>
      <tr><td>Fill Capacity</td><td>5CF / 150L</td><td>9CF / 250L</td><td>13CF / 375L</td><td>22CF / 625L</td><td>44CF / 1250L</td><td>66CF / 1875L</td><td>88CF / 2500L</td><td>132CF / 3750L</td></tr>
      <tr><td>Weight</td><td>440lbs</td><td>550lbs</td><td>770lbs</td><td>1212lbs</td><td>1874lbs</td><td>2645lbs</td><td>3527lbs</td><td>5511lbs</td></tr>
      <tr><td>Motor Size</td><td>4hp</td><td>5.3hp</td><td>6.7hp</td><td>10hp</td><td>14.75hp</td><td>20hp</td><td>25hp</td><td>30hp</td></tr>
      <tr><td>Total Length</td><td>50"</td><td>53.5"</td><td>63"</td><td>72"</td><td>94"</td><td>102"</td><td>131.5"</td><td>157.5"</td></tr>
      <tr><td>Total Width</td><td>28"</td><td>34"</td><td>41.5"</td><td>45"</td><td>52"</td><td>66"</td><td>52.5"</td><td>54"</td></tr>
      <tr><td>Total Height</td><td>66"</td><td>69"</td><td>71"</td><td>82"</td><td>87"</td><td>95"</td><td>76"</td><td>110"</td></tr>
      <tr><td>Tub Length</td><td>31.5"</td><td>35.5"</td><td>41"</td><td>47"</td><td>59"</td><td>70"</td><td>75"</td><td>100"</td></tr>
      <tr><td>Tub Width</td><td>16.5"</td><td>22"</td><td>25"</td><td>27.5"</td><td>35.5"</td><td>39"</td><td>48"</td><td>48"</td></tr>
      <tr><td>Tub Height</td><td>20.5"</td><td>26"</td><td>28"</td><td>33"</td><td>41"</td><td>46"</td><td>51"</td><td>53"</td></tr>
      <tr><td>Shaft Diameter</td><td>2"</td><td>2-1/4"</td><td>2-5/8"</td><td>3"</td><td>3.5"</td><td>4"</td><td>4"</td><td>5-1/4"</td></tr>
      <tr><td>Tub Thickness</td><td>3mm</td><td>3mm</td><td>3mm</td><td>4mm</td><td>4mm</td><td>5mm</td><td>5mm</td><td>6mm</td></tr>
      <tr><td>Ribbon Thickness</td><td>6mm</td><td>8mm</td><td>8mm</td><td>8mm</td><td>10mm</td><td>12mm</td><td>12mm</td><td>14mm</td></tr>
      <tr><td>Max RPM</td><td>46 rpm</td><td>46 rpm</td><td>46 rpm</td><td>46 rpm</td><td>30 rpm</td><td>31 rpm</td><td>32 rpm</td><td>33 rpm</td></tr>
    </table>
  </div>
</section>

</body>
</html>
```